Aunt Wilma's Ember-Kissed Husk Shack Concession Trailer Logo Wraps

Looking to put my design concept into a final production-ready format for vinyl-based logo "wrap" on the exterior of a 7x12 black concession trailer selling farm-fresh corn on the cob slathered in flavor flamboyance, corn in a cup, corn over crushed snacks (Crunvels, Zaplins, Puffnars, etc.) served in the bags, fire-roasted street corn (Mexican elotes), corn grits, corn chowder, cornbread, corndogs. I have my fonts and colors and a flame graphic I've roughly edited/reworked attempting to make it work and need a design pro to bring it all together for me. The approximate size of the graphics on the four sides of the trailer will be: the serving window when closed (48"L x 24"H); front (48"x48"); full right side (11'x5'); door (6'x2') and possibly the left side next to door (3'x5'). Pictures uploaded.
Target Market(s)
Food truck festivals, private catering gigs, fairs, farm markets, concerts, etc.
Font styles to use
Other font styles liked:
- flame fetish, Algerian
Requirements
Must have
- My color scheme as depicted in uploaded files, flame fetish font uploaded (will consider similar fonts), flame/fire artwork, bright bold colors that pop against a black background
Nice to have
- straight line of flames on each side of the "fire-roasted" text, flowing from the first and last letter

```html
<!DOCTYPE html>
<html lang="en">
<head>
<meta charset="utf-8">
<title>Aunt Wilma's Ember-Kissed Husk Shack – Trailer Wrap</title>
<link rel="stylesheet" href="https://fonts.googleapis.com/css2?family=Yellowtail&family=Kaushan+Script&family=Lilita+One&display=swap">
<style>
  :root {
    --stage: #e9e9e6;
    --wrap-black: #050505;
    --sky-blue: #14a0e4;
    --ember-orange: #f26a1b;
    --ember-red: #d81e25;
    --corn-yellow: #f7ec2a;
    --flame-orange: #f7931e;
  }
  * { margin: 0; padding: 0; box-sizing: border-box; }
  html, body {
    width: 1200px;
    height: 981px;
    overflow: hidden;
    background: var(--stage);
  }
  .wrap-panel {
    position: absolute;
    left: 30px;
    top: 190px;
    width: 1140px;
    height: 600px;
    background: var(--wrap-black);
    overflow: hidden;
  }
  .owner-name {
    position: absolute;
    top: 24px;
    width: 100%;
    text-align: center;
    font-family: "Yellowtail", cursive;
    font-weight: 400;
    font-size: 120px;
    line-height: 1;
    color: var(--sky-blue);
  }
  .roast-style {
    position: absolute;
    top: 172px;
    width: 100%;
    text-align: center;
    font-family: "Kaushan Script", cursive;
    font-size: 92px;
    line-height: 1;
    color: var(--ember-orange);
  }
  .flame-strip {
    position: absolute;
    top: 300px;
    width: 150px;
    height: 22px;
    border-radius: 11px;
    background: linear-gradient(to right, var(--ember-red), var(--flame-orange), var(--corn-yellow));
  }
  .flame-strip.left { left: 30px; }
  .flame-strip.right {
    right: 30px;
    background: linear-gradient(to left, var(--ember-red), var(--flame-orange), var(--corn-yellow));
  }
  .main-offer {
    position: absolute;
    top: 330px;
    width: 100%;
    text-align: center;
    font-family: "Lilita One", sans-serif;
    font-size: 140px;
    line-height: 1;
    letter-spacing: 4px;
    color: var(--corn-yellow);
    text-shadow: 6px 6px 0 var(--ember-red);
  }
  .tagline {
    position: absolute;
    top: 510px;
    width: 100%;
    text-align: center;
    font-family: "Kaushan Script", cursive;
    font-size: 40px;
    line-height: 1;
    color: var(--sky-blue);
  }
</style>
</head>
<body>
  <main class="wrap-panel">
    <h1 class="owner-name">Aunt Wilma's</h1>
    <div class="flame-strip left" role="img" aria-label="Line of orange and yellow flames"></div>
    <div class="flame-strip right" role="img" aria-label="Line of orange and yellow flames"></div>
    <p class="roast-style">ember-kissed</p>
    <p class="main-offer">HUSK SHACK</p>
    <p class="tagline">fresh husk corn dripping in buttery bold spice</p>
  </main>
</body>
</html>
```